Accountability Project Graphics

I want to create 10 social media graphics (new Instagram size 4:5 (1080 x 1350 pixels) focusing on our Quilvo Accountability App, using any of the 3 pictures attached. Use the attached pics only, NO RANDOM STOCK PHOTOGRAPHY. For the color scheme, use the landing page colors/fonts (attached).
You can add any of the 3 photos attached but I mainly need BOLD text that includes these headlines and sub-headlines on them.
Please NOTE for all the headlines below, also add this sub-headline on each graphic:
Stay Consistent with RT in Your Pocket!
Here are the headlines:
• Stop Starting Over Every Monday
• You don't need more willpower. You need more support
• Built for women who are tired of doing this alone
• When Motivation Fades, RT Checks In
• The Support System You've Been Missing
• Support When Motivation Disappears
• What if RT Checked in Every Day?
• The Missing Piece Isn't Another Diet
• Eat the food you love. Stay accountable every day.
• One Bad Meal Doesn't Mean You Failed
women over 40 trying to lose weight

```html
<!DOCTYPE html>
<html lang="en">
<head>
<meta charset="utf-8">
<title>Accountability Social Graphics</title>
<link rel="stylesheet" href="https://fonts.googleapis.com/css2?family=Libre+Baskerville:ital,wght@0,700;1,700&family=Arimo:wght@700&display=swap">
<style>
:root{
  --canvas:#6b6b6b;
  --paper:#fdf1f1;
  --ink:#2b1636;
  --rose:#c95a7c;
  --rose-line:#ec6fa0;
  --plum:#6a1f58;
  --plum-deep:#3d0f3a;
  --photo-a:#c9a596;
  --photo-b:#5a3a45;
}
*{margin:0;padding:0;box-sizing:border-box}
html,body{width:1200px;height:3484px;overflow:hidden;background:var(--canvas)}
.sheet{position:relative;width:1200px;height:3484px}
.card{position:absolute;width:494px;height:618px;background:linear-gradient(160deg,var(--plum),var(--plum-deep));overflow:hidden}
.col-left{left:88px}.col-right{left:630px}
.row-1{top:106px}.row-2{top:766px}.row-3{top:1425px}.row-4{top:2084px}.row-5{top:2743px}
.panel{position:absolute;inset:0;background:var(--paper)}
.curve-tr{right:14px;border-top-right-radius:90px}
.curve-tl{left:14px;border-top-left-radius:90px}
.curve-br{right:14px;bottom:0;border-bottom-right-radius:90px}
.curve-bl{left:14px;border-bottom-left-radius:90px}
.curve-bl-big{left:14px;border-bottom-left-radius:120px}
.headline{position:absolute;font-family:"Libre Baskerville",Georgia,serif;font-weight:700;color:var(--ink);white-space:nowrap}
.headline em,.accent{font-style:italic;color:var(--rose)}
.tagline{position:absolute;font-family:Arimo,Arial,sans-serif;font-weight:700;color:var(--ink);white-space:nowrap}
.tagline span{color:var(--rose)}
.underline{position:absolute;left:0;height:5px;width:390px;background:var(--rose-line);border-radius:3px}
.photo{position:absolute;background:linear-gradient(150deg,var(--photo-a),var(--photo-b))}
.pill{position:absolute;left:22px;top:559px;width:453px;height:51px;border-radius:26px;background:var(--plum-deep);color:#fff;font-family:Arimo,Arial,sans-serif;font-weight:700;font-size:20px;display:flex;align-items:center;justify-content:center}
.pill span{color:var(--rose-line);margin:0 5px}
</style>
</head>
<body>
<main class="sheet">

  <section class="card col-left row-1">
    <div class="panel curve-tr"></div>
    <h2 class="headline" style="left:44px;top:28px;font-size:64px;line-height:78px"><span class="accent" style="font-style:normal">Stop</span><br>Starting<br>Over Every<br><em>Monday</em></h2>
    <p class="tagline" style="left:44px;top:430px;font-size:36px;line-height:48px">Stay Consistent with<br><span>RT in Your Pocket!</span></p>
    <div class="underline" style="top:551px"></div>
  </section>

  <section class="card col-right row-1">
    <div class="panel curve-tl"></div>
    <h2 class="headline" style="left:53px;top:22px;font-size:44px;line-height:54px">You don't need<br>more willpower.</h2>
    <p class="headline accent" style="left:53px;top:148px;font-size:48px;line-height:56px">You need more</p>
    <p class="headline accent" style="left:53px;top:196px;font-size:78px;line-height:90px">Support</p>
    <div class="photo" role="img" aria-label="Two women sharing a joyful hug" style="left:191px;top:273px;width:303px;height:345px;border-radius:150px 150px 0 0"></div>
    <p class="tagline" style="left:24px;top:398px;font-size:28px;line-height:36px">Stay<br>Consistent<br>with<br><span>RT in Your<br>Pocket!</span></p>
  </section>

  <section class="card col-left row-2">
    <div class="panel curve-br"></div>
    <h2 class="headline" style="left:27px;top:32px;font-size:82px;line-height:100px">Built for<br>Women</h2>
    <div class="photo" role="img" aria-label="Coach standing with a smiling client" style="left:0;top:235px;width:298px;height:267px;border-radius:0 140px 140px 0"></div>
    <p class="headline accent" style="left:323px;top:235px;font-size:42px;line-height:49px">who<br>are<br>tired<br>of<br>doing<br>this<br>alone</p>
    <p class="tagline" style="left:18px;top:522px;font-size:26px;line-height:35px">Stay Consistent with<br><span>RT in Your Pocket!</span></p>
  </section>

  <section class="card col-right row-2">
    <div class="panel curve-bl"></div>
    <div class="photo" role="img" aria-label="Coach standing in a lounge, hand on hip" style="left:256px;top:0;width:238px;height:382px;border-radius:0 0 0 120px"></div>
    <h2 class="headline" style="left:25px;top:24px;font-size:42px;line-height:52px">When<br>Motivation<br>Fades,</h2>
    <p class="headline accent" style="left:25px;top:186px;font-size:62px;line-height:72px">RT<br>Checks<br>In</p>
    <p class="tagline" style="left:28px;top:470px;font-size:36px;line-height:48px">Stay Consistent with<br><span>RT in Your Pocket!</span></p>
  </section>

  <section class="card col-left row-3">
    <div class="panel curve-tr"></div>
    <h2 class="headline" style="left:28px;top:50px;font-size:56px;line-height:74px">The Support<br>System<br><em>You've Been<br>Missing</em></h2>
    <p class="tagline" style="left:44px;top:430px;font-size:36px;line-height:48px">Stay Consistent with<br><span>RT in Your Pocket!</span></p>
    <div class="underline" style="top:551px"></div>
  </section>

  <section class="card col-right row-3">
    <div class="panel curve-tl"></div>
    <h2 class="headline" style="left:57px;top:18px;font-size:90px;line-height:104px">Support</h2>
    <p class="headline accent" style="left:57px;top:128px;font-size:44px;line-height:75px">When Motivation<br>Disappears</p>
    <div class="photo" role="img" aria-label="Two women sharing a joyful hug" style="left:5px;top:273px;width:311px;height:345px;border-radius:155px 155px 0 0"></div>
    <p class="tagline" style="left:318px;top:392px;font-size:28px;line-height:36px">Stay<br>Consistent<br>with<br><span>RT in Your<br>Pocket!</span></p>
  </section>

  <section class="card col-left row-4">
    <div class="panel curve-br"></div>
    <div class="photo" role="img" aria-label="Coach standing, hand on hip" style="left:264px;top:95px;width:216px;height:515px;border-radius:100px 100px 30px 30px"></div>
    <h2 class="headline" style="left:27px;top:14px;font-size:56px;line-height:68px">What if <em style="font-style:normal">RT</em><br>Checked<br>in</h2>
    <p class="headline accent" style="left:27px;top:232px;font-size:80px;line-height:96px">Every<br>Day?</p>
    <p class="tagline" style="left:27px;top:480px;font-size:30px;line-height:40px">Stay Consistent<br>with <span>RT in Your<br>Pocket!</span></p>
  </section>

  <section class="card col-right row-4">
    <div class="panel curve-bl-big"></div>
    <h2 class="headline" style="left:38px;top:30px;font-size:56px;line-height:90px">The Missing<br>Piece Isn't<br><em>Another<br>Diet</em></h2>
    <p class="tagline" style="left:42px;top:426px;font-size:36px;line-height:48px">Stay Consistent with<br><span>RT in Your Pocket!</span></p>
  </section>

  <section class="card col-left row-5">
    <div class="panel curve-tr"></div>
    <h2 class="headline" style="left:27px;top:28px;font-size:56px;line-height:78px">Eat the food<br><em>you love.</em><br><span style="font-size:60px">Stay<br>accountable</span><br><em style="font-size:60px">every day</em></h2>
    <p class="tagline" style="left:44px;top:476px;font-size:36px;line-height:48px">Stay Consistent with<br><span>RT in Your Pocket!</span></p>
    <div class="underline" style="top:583px"></div>
  </section>

  <section class="card col-right row-5">
    <div class="panel curve-tl"></div>
    <h2 class="headline" style="left:0;width:494px;text-align:center;top:30px;font-size:54px;line-height:70px">One Bad Meal<br>Doesn't Mean<br><em>You Failed</em></h2>
    <div class="photo" role="img" aria-label="Coach and client laughing together" style="left:82px;top:261px;width:329px;height:298px;border-radius:60px 60px 0 0"></div>
    <p class="pill">Stay Consistent with <span>RT in Your Pocket!</span></p>
  </section>

</main>
</body>
</html>
```